Creating a website for a life changing company (Halvra Q)

We do need a website for our Coaching and Consulting business we recently launched. We do need it for information purposes and that our clients do have the opportunity to subscribe for packages, programs etc.
We would like to see designs which use the colours blue and yellow (see attachment). The final design should communicate our passion for the potential in people and the benefit (rising onward) for them.
Updates
Additional information:
Our company (webpage): Halvra Q (the C stands for "what people cannot see / imagine now...)
Welcome to Halvra Q(uarry)
Consulting (O.R.T.) & Coaching (Rise onward)
Two pillars:
1) O.R.T. ( Steward pathway - Our program - focussing on companies - business orientated)
2) Rise onward (Daily renewal - Events - focusing on individuals - primarily life changing)
For both of them we offer: Lanternhall & Halvra Q+ (This should go as a subscription)
Eventually you can draft this as a rhombus
Industry/Entity Type
Coaching / Consulting
Coding
Coded - Design and coding required
Number of Pages Required
1 page
Font styles to use
Other font styles liked:
- Lato
Requirements
Must have
- Please see attachment (About us / Offers / Calendar function / Links to Instagram and LinkedIn account / mailing list / page for clients
Nice to have
- A banner

```html
<!DOCTYPE html>
<html lang="en">
<head>
<meta charset="utf-8">
<title>Halvra Q — Coaching &amp; Consulting</title>
<link href="https://fonts.googleapis.com/css2?family=Lato:wght@400;700;900&display=swap" rel="stylesheet">
<style>
:root{
  --navy:#1f3556;
  --navy-deep:#172a45;
  --yellow:#f5bf2a;
  --ice:#e4edf8;
  --cream:#fbfde9;
  --ink:#2b2f38;
  --muted:#7a808a;
  --line:#d9dde3;
  --white:#ffffff;
}
*{box-sizing:border-box;margin:0;padding:0}
html,body{width:1200px;height:4440px;overflow:hidden}
body{font-family:"Lato",sans-serif;color:var(--ink);background:var(--white);position:relative}
section,header,footer,nav{position:relative;width:1200px}
.abs{position:absolute}

/* top bar */
.topbar{height:72px;background:var(--navy)}
.brand{position:absolute;left:120px;top:26px}
.brand-name{font-weight:900;font-size:16px;letter-spacing:2px;color:var(--white)}
.top-contact{position:absolute;left:720px;top:28px;font-size:13px;color:var(--white);letter-spacing:.5px}
.top-contact span{margin:0 12px;opacity:.6}
.socials{position:absolute;display:flex;gap:10px}
.topbar .socials{left:1020px;top:22px}
.social{width:28px;height:28px;border-radius:50%;background:var(--yellow)}
.social.alt{background:#4a7fc1}

/* nav */
.mainnav{height:68px;background:var(--white);box-shadow:0 2px 8px rgba(0,0,0,.06)}
.mainnav ul{list-style:none;display:flex;gap:48px;position:absolute;left:260px;top:26px}
.mainnav a{font-size:13px;font-weight:900;color:var(--navy);text-decoration:none;letter-spacing:.5px}
.mainnav a.active{color:var(--yellow)}

/* hero */
.hero{height:612px;background:linear-gradient(110deg,#3a352f 0%,#6b5a48 35%,#8d7a66 60%,#4a3e34 100%)}
.hero-shade{position:absolute;inset:0;background:linear-gradient(90deg,rgba(20,25,35,.55),rgba(20,25,35,.1) 70%)}
.hero h1{position:absolute;left:260px;top:240px;font-size:32px;font-weight:900;color:var(--white);letter-spacing:.5px}
.hero p{position:absolute;left:260px;top:290px;width:420px;font-size:18px;line-height:1.4;color:var(--white);font-weight:700}
.btn{display:inline-block;background:var(--yellow);color:var(--navy);font-weight:900;font-size:12px;letter-spacing:.8px;border-radius:22px;text-align:center;text-decoration:none}
.hero .btn{position:absolute;left:260px;top:372px;width:150px;height:44px;line-height:44px}
.slide-arrows{position:absolute;left:1010px;top:514px;display:flex;gap:14px}
.slide-arrows svg{width:36px;height:36px}

/* section titles */
.title{position:absolute;left:0;width:1200px;text-align:center;font-size:36px;font-weight:900;color:var(--navy);letter-spacing:.5px}
.title::after{content:"";display:block;width:60px;height:4px;background:var(--yellow);margin:10px auto 0;border-radius:2px}

/* about */
.about{height:668px}
.about-art{position:absolute;left:100px;top:120px;width:420px;height:420px;overflow:visible}
.about-photo{position:absolute;left:130px;top:150px;width:360px;height:360px;border-radius:50%;background:radial-gradient(circle at 45% 40%,#c9a98a,#7b6350 60%,#4d3f35)}
.about-text{position:absolute;left:640px;top:150px;width:460px}
.about-text h2{font-size:28px;font-weight:900;color:var(--navy)}
.about-text h2::after{content:"";display:block;width:60px;height:4px;background:var(--yellow);margin-top:8px;border-radius:2px}
.about-text p{font-size:13px;line-height:1.85;color:var(--muted);margin-top:22px}
.about-text .btn{margin-top:30px;width:150px;height:44px;line-height:44px}

/* lanternhall */
.lanternhall{height:612px;background:var(--ice)}
.lead{position:absolute;left:220px;top:170px;width:760px;text-align:center;font-size:13px;line-height:1.7;color:var(--muted)}
.service{position:absolute;top:248px;width:304px;height:312px;background:var(--white);box-shadow:0 6px 18px rgba(31,53,86,.12)}
.service .ph{position:absolute;left:12px;top:12px;width:280px;height:208px}
.service h3{position:absolute;left:0;top:240px;width:100%;text-align:center;font-size:16px;font-weight:900;color:var(--yellow);letter-spacing:1px}

/* programs */
.programs{height:748px}
.program{position:absolute;width:212px;height:284px;background:var(--white);box-shadow:0 6px 20px rgba(31,53,86,.16);text-align:center}
.program .ph{width:130px;height:130px;border-radius:50%;margin:24px auto 0}
.program h3{margin-top:18px;font-size:16px;font-weight:900;color:var(--navy)}
.program h3::after{content:"";display:block;width:40px;height:3px;background:var(--yellow);margin:8px auto 0}
.program p{margin:12px 18px 0;font-size:12px;line-height:1.6;color:var(--muted)}
.book{position:absolute;left:520px;top:628px;width:160px;height:44px;line-height:44px;display:flex;align-items:center;justify-content:center;gap:8px}

/* what we do */
.whatwedo{height:720px;background:var(--cream)}
.tabs{position:absolute;left:360px;top:176px;display:flex;gap:20px}
.tab{width:140px;height:44px;line-height:44px;border-radius:22px;background:var(--white);box-shadow:0 4px 12px rgba(0,0,0,.1);text-align:center;font-size:12px;font-weight:900;color:var(--navy)}
.tab.on{background:var(--yellow)}
.work{position:absolute;top:248px;width:308px;height:376px;background:var(--white);box-shadow:0 6px 18px rgba(0,0,0,.1);text-align:center}
.work .ph{position:absolute;left:12px;top:12px;width:284px;height:208px}
.work h3{position:absolute;top:236px;width:100%;font-size:16px;font-weight:900;color:var(--navy)}
.work h3::after{content:"";display:block;width:40px;height:3px;background:var(--yellow);margin:8px auto 0}
.work p{position:absolute;top:276px;left:26px;right:26px;font-size:12px;line-height:1.65;color:var(--muted)}

/* packages */
.packages{height:660px}
.plan{position:absolute;width:380px;height:380px;border-radius:50%;background:var(--white);border:2px solid var(--line);overflow:hidden;text-align:center}
.plan .body{position:absolute;top:0;width:100%}
.plan.left .body{left:-40px}
.plan.right .body{left:40px}
.plan .price{margin-top:58px;font-size:42px;font-weight:700;color:var(--yellow)}
.plan h3{margin-top:6px;font-size:20px;font-weight:900;color:var(--navy)}
.plan p{margin:12px 92px 0;font-size:12px;line-height:1.6;color:var(--muted)}
.plan.featured p{margin:12px 64px 0}
.plan .cap{position:absolute;left:0;bottom:0;width:100%;height:64px;background:var(--yellow);display:flex;justify-content:center;padding-top:14px}
.plan.left .cap{padding-right:80px}
.plan.right .cap{padding-left:80px}
.plan.featured{background:var(--yellow);border-color:var(--yellow);z-index:2;box-shadow:0 8px 24px rgba(0,0,0,.12)}
.plan.featured .price{color:var(--white)}
.plan.featured p{color:var(--navy)}
.plan.featured .cap{background:var(--white)}

/* footer */
.footer{height:240px;background:var(--navy);color:var(--white)}
.foot-brand{position:absolute;left:120px;top:106px}
.foot-col{position:absolute;top:28px}
.foot-col h4{font-size:14px;font-weight:900;letter-spacing:.5px}
.foot-col ul{list-style:none;margin-top:14px}
.foot-col li{font-size:12px;line-height:22px;display:flex;align-items:center;gap:10px}
.foot-col li::before{content:"";width:9px;height:9px;border-radius:50%;background:var(--yellow)}
.contact-item{margin-top:12px;display:flex;gap:10px;font-size:12px;line-height:1.5}
.contact-item svg{flex:none;width:16px;height:16px;margin-top:2px}
.contact-item b{display:block;font-weight:900}
.signup{margin-top:18px;display:flex;width:300px;height:38px;background:var(--white);border-radius:19px;overflow:hidden}
.signup span{flex:1;padding-left:16px;line-height:38px;font-size:12px;color:var(--muted)}
.signup b{width:110px;background:var(--yellow);color:var(--navy);text-align:center;line-height:38px;font-size:12px;font-weight:900}
.footer .socials{position:static;margin-top:16px}
.legal{height:40px;background:var(--navy-deep);color:#aeb7c6;font-size:12px;text-align:center;line-height:40px}
</style>
</head>
<body>

<header class="topbar">
  <div class="brand"><span class="brand-name">HALVRA Q</span></div>
  <div class="top-contact">+1 (000) 000 0000<span>|</span>CONTACT US</div>
  <div class="socials"><div class="social alt" role="img" aria-label="Professional network profile"></div><div class="social" role="img" aria-label="Photo sharing profile"></div></div>
</header>

<nav class="mainnav">
  <ul>
    <li><a class="active" href="#">HOME</a></li>
    <li><a href="#">ABOUT US</a></li>
    <li><a href="#">O.R.T.</a></li>
    <li><a href="#">LANTERNHALL</a></li>
    <li><a href="#">RISE ONWARD</a></li>
    <li><a href="#">HALVRA Q+</a></li>
  </ul>
</nav>

<section class="hero">
  <div class="abs" style="inset:0" role="img" aria-label="Coaching session between a coach and a client in a bright office"></div>
  <div class="hero-shade"></div>
  <h1>WELCOME TO HALVRA Q</h1>
  <p>Sed ut perspiciatis unde omnis iste natus err or sit voluptatem accusa.</p>
  <a class="btn" href="#">GET A QUOTE</a>
  <div class="slide-arrows">
    <svg viewBox="0 0 36 36"><circle cx="18" cy="18" r="16" fill="none" stroke="#fff" stroke-width="1.5" opacity=".7"/><path d="M21 11l-7 7 7 7" fill="none" stroke="#fff" stroke-width="2"/></svg>
    <svg viewBox="0 0 36 36"><circle cx="18" cy="18" r="16" fill="none" stroke="#fff" stroke-width="1.5" opacity=".7"/><path d="M15 11l7 7-7 7" fill="none" stroke="#fff" stroke-width="2"/></svg>
  </div>
</section>

<section class="about">
  <svg class="about-art" viewBox="0 0 420 420"><path d="M330 62 A200 200 0 1 0 330 358" fill="none" stroke="var(--yellow)" stroke-width="22"/></svg>
  <div class="about-photo" role="img" aria-label="Team gathered around a table in a workshop"></div>
  <div class="about-text">
    <h2>ABOUT HALVRA</h2>
    <p>Lorem ipsum dolor sit amet, consectetur adipiscing elit, sed do eiusmod tempor incididunt ut labore et dolore magna aliqua. Ut enim ad minim veniam, quis nostrud exercitation ullamco laboris nisi ut aliquip ex ea commodo consequat. Duis aute irure dolor in reprehenderit in voluptate velit esse.</p>
    <p>Labore et dolore magna aliqua. Ut enim ad minim veniam, quis nostrud exercitation ullamco laboris nisi ut aliquip ex ea commodo consequat. Duis aute irure dolor in voluptate velit esse.</p>
    <a class="btn" href="#">LEARN MORE</a>
  </div>
</section>

<section class="lanternhall">
  <h2 class="title" style="top:88px">LANTERNHALL</h2>
  <p class="lead">Lorem ipsum dolor sit amet, consectetur adipiscing elit, sed do eiusmod tempor incididunt ut labore et dolore magna aliqua. Ut enim ad minim veniam, quis nostrud exercitation ullamco laboris nisi ut aliquip ex ea commodo.</p>
  <div class="service" style="left:112px"><div class="ph" style="background:linear-gradient(135deg,#a9b6c4,#6e7c8c)" role="img" aria-label="Coach talking with a client"></div><h3>COACHING</h3></div>
  <div class="service" style="left:448px"><div class="ph" style="background:linear-gradient(135deg,#b88f6a,#5d4636)" role="img" aria-label="Consultants meeting around a desk"></div><h3>CONSULTING</h3></div>
  <div class="service" style="left:784px"><div class="ph" style="background:linear-gradient(135deg,#c4c8cf,#7d8590)" role="img" aria-label="Relaxed conversation by a fireside"></div><h3>FIRESIDE CHAT</h3></div>
</section>

<section class="programs">
  <h2 class="title" style="top:96px">OUR PROGRAMS</h2>
  <div class="program" style="left:112px;top:188px"><div class="ph" style="background:linear-gradient(135deg,#8a7766,#3e3530)" role="img" aria-label="Program portrait"></div><h3>LOREM IPSUM</h3><p>Lorem ipsum dolor sit amet, conse ectetur adipiscing elit, sed do ei usmod tempor incidu.</p></div>
  <div class="program" style="left:364px;top:228px"><div class="ph" style="background:linear-gradient(135deg,#9aa6b4,#4f5a68)" role="img" aria-label="Program portrait"></div><h3>LOREM IPSUM</h3><p>Lorem ipsum dolor sit amet, conse ectetur adipiscing elit, sed do ei usmod tempor incidu.</p></div>
  <div class="program" style="left:620px;top:196px"><div class="ph" style="background:linear-gradient(135deg,#8da0b8,#3c4a5e)" role="img" aria-label="Program portrait"></div><h3>LOREM IPSUM</h3><p>Lorem ipsum dolor sit amet, conse ectetur adipiscing elit, sed do ei usmod tempor incidu.</p></div>
  <div class="program" style="left:872px;top:236px"><div class="ph" style="background:linear-gradient(135deg,#b3b7bd,#5b6068)" role="img" aria-label="Program portrait"></div><h3>LOREM IPSUM</h3><p>Lorem ipsum dolor sit amet, conse ectetur adipiscing elit, sed do ei usmod tempor incidu.</p></div>
  <a class="btn book" href="#"><svg width="14" height="14" viewBox="0 0 14 14"><rect x="1" y="2.5" width="12" height="10.5" rx="1.5" fill="none" stroke="var(--navy)" stroke-width="1.6"/><path d="M1 6h12M4 1v3M10 1v3" stroke="var(--navy)" stroke-width="1.6"/></svg>BOOK NOW</a>
</section>

<section class="whatwedo">
  <h2 class="title" style="top:80px">WHAT WE DO</h2>
  <div class="tabs"><div class="tab">RISE ONWARD</div><div class="tab on">HALVRA Q+</div><div class="tab">O.R.T.</div></div>
  <div class="work" style="left:112px"><div class="ph" style="background:linear-gradient(135deg,#6d6258,#2f2a27)" role="img" aria-label="Colleagues sharing insights at a table"></div><h3>COACHING INSIGHTS</h3><p>Sed ut perspiciatis unde omnis iste natus error sit voluptatem accusant doloremque laudantium totam.</p></div>
  <div class="work" style="left:446px"><div class="ph" style="background:linear-gradient(135deg,#8a9098,#3d4249)" role="img" aria-label="Group meeting in a modern office"></div><h3>GRAB AND GO</h3><p>Sed ut perspiciatis unde omnis iste natus error sit voluptatem accusant doloremque laudantium totam.</p></div>
  <div class="work" style="left:780px"><div class="ph" style="background:linear-gradient(135deg,#b59a7e,#5e4a3a)" role="img" aria-label="Team working on laptops together"></div><h3>BE RESOURCEFUL</h3><p>Sed ut perspiciatis unde omnis iste natus error sit voluptatem accusant doloremque laudantium totam.</p></div>
</section>

<section class="packages">
  <h2 class="title" style="top:80px">OUR PACKAGES</h2>
  <div class="plan left" style="left:142px;top:208px"><div class="body"><div class="price">$20</div><h3>BASIC PLAN</h3><p>Sed ut perspiciatis unde omnis iste natus error sit voluptatem accusant laudan totam rem aperiam eaque ipsa.</p></div><div class="cap"><svg width="28" height="16" viewBox="0 0 28 16"><path d="M2 8h22M18 2l6 6-6 6" fill="none" stroke="var(--navy)" stroke-width="2.4"/></svg></div></div>
  <div class="plan featured" style="left:410px;top:196px"><div class="body"><div class="price">$40</div><h3>ADVANCED PLAN</h3><p>Sed ut perspiciatis unde omnis iste natus error sit voluptatem accusant doloremque laudan totam rem aperiam eaque ipsa.</p></div><div class="cap"><svg width="28" height="16" viewBox="0 0 28 16"><path d="M2 8h22M18 2l6 6-6 6" fill="none" stroke="var(--navy)" stroke-width="2.4"/></svg></div></div>
  <div class="plan right" style="left:682px;top:208px"><div class="body"><div class="price">$30</div><h3>PREMIUM PLAN</h3><p>Sed ut perspiciatis unde omnis iste natus error sit voluptatem accusant laudan totam rem aperiam eaque ipsa.</p></div><div class="cap"><svg width="28" height="16" viewBox="0 0 28 16"><path d="M2 8h22M18 2l6 6-6 6" fill="none" stroke="var(--navy)" stroke-width="2.4"/></svg></div></div>
</section>

<footer class="footer">
  <div class="foot-brand"><span class="brand-name">HALVRA Q</span></div>
  <div class="foot-col" style="left:340px">
    <h4>NAVIGATION</h4>
    <ul><li>Home</li><li>About Us</li><li>O.R.T.</li><li>Lanternhall</li><li>Rise Onward</li><li>Halvra Q+</li></ul>
  </div>
  <div class="foot-col" style="left:540px;width:200px">
    <h4>CONTACT</h4>
    <div class="contact-item"><svg viewBox="0 0 16 16"><path d="M8 15s5-5 5-9A5 5 0 0 0 3 6c0 4 5 9 5 9z" fill="var(--yellow)"/><circle cx="8" cy="6" r="2" fill="var(--navy)"/></svg><div><b>ADDRESS:</b>12 Lorem Ipsum Dolor,<br>Sit Amet State</div></div>
    <div class="contact-item"><svg viewBox="0 0 16 16"><path d="M4 1l3 3-2 2c1 2 3 4 5 5l2-2 3 3-2 3C7 15 1 9 1 3z" fill="var(--yellow)"/></svg><div><b>PHONE:</b>+1 (000) 000 0000</div></div>
    <div class="contact-item"><svg viewBox="0 0 16 16"><rect x="1" y="3" width="14" height="10" rx="1" fill="var(--yellow)"/><path d="M1 4l7 5 7-5" fill="none" stroke="var(--navy)" stroke-width="1.4"/></svg><div><b>E-MAIL:</b>hello@halvraq.example</div></div>
  </div>
  <div class="foot-col" style="left:768px">
    <h4>NEWSLETTER SIGNUP</h4>
    <div class="signup"><span>Email Address</span><b>SIGN UP</b></div>
    <div class="socials"><div class="social alt" role="img" aria-label="Professional network profile"></div><div class="social" role="img" aria-label="Photo sharing profile"></div></div>
  </div>
</footer>
<div class="legal">© 2022 HALVRA Q &nbsp;|&nbsp; All Rights Reserved</div>

</body>
</html>
```